Web Design Project - Shipping Industry

Goals and Objectives
The objective of the new website is to create a more modern look and feel. The site will also allow for a more effective means of communicating with members while providing the public with information and developments in the local, regional and international shipping industry.
Scope
The website will highlight the history of the organisation inclusive of text and photographs. It will take visitors through the years from beginning to present. Information on the history of the shipping industry will also be included.
It will feature current articles on the organisation, its members and stakeholders in the shipping industry. Member information as well as pertinent details regarding the organisation’s subsidiaries will be documented for the website.
Information as it relates to shipping statistics, case studies, laws and regulations, international treaties and trade documents, shipping terms, careers in shipping, job opportunities, training opportunities, information for shippers including port listing and trade lanes will be main features of the content for the website.
The Association’s community involvement, industry calendar events and related links relevant industry members will also be featured.
Target Market
• The General Public;
• Members of the organization;
• Shipping Industry Stakeholders (local, regional and international);
• Tertiary students conducting research.
• Potential employees
• Potential Business Partners
Best Practice Bench Marketing
The following websites are being looked at:
• Korvel Quayworks - http://www.korvelquayworks.example/ (preferred look)
• Tessaly Maritime Association - http://www.tma-freight.example/ (like image transition on main page)
• Drovna - http://www.drovna.example (professional look)
• PLW - http://www.pelworth.example (preferred color: blue in logo)
• Quillo - http://www.quillo.example/electronics/tv-video-audio/ (preferred look for links page: image + short text below + visit site link)
Expected Result
• 3 - 5 pages which must include: [1] main page [2] standard page [3] links page

```html
<!DOCTYPE html>
<html lang="en">
<head>
<meta charset="utf-8">
<title>The Pelworth Shipping Association – About Us</title>
<link href="https://fonts.googleapis.com/css2?family=Questrial&family=Open+Sans:wght@400;600;700&family=Alfa+Slab+One&display=swap" rel="stylesheet">
<style>
:root{
  --navy:#0a3d9c;
  --navy-dark:#062c7a;
  --link:#1646a8;
  --orange:#f4a20a;
  --text:#333;
  --muted:#777;
  --side:#d6e1f4;
  --rule:#cfcfcf;
  --footer:#c9c9c9;
  --white:#fff;
}
*{box-sizing:border-box;margin:0;padding:0}
html,body{width:1008px;height:1200px;overflow:hidden;background:var(--white)}
body{position:relative;font-family:"Open Sans",sans-serif;color:var(--text);font-size:10px}
.abs{position:absolute}

/* header */
.brand-mark{left:101px;top:24px;width:64px;height:64px;border-radius:50%;background:var(--navy)}
.brand-name{left:101px;top:99px;font-family:"Questrial",sans-serif;font-size:20px;color:var(--navy-dark)}
.login-label{left:403px;top:23px;font-size:11px;letter-spacing:.6px;color:var(--navy-dark)}
.field{top:18px;width:159px;height:22px;border:1px solid #bbb;border-radius:11px;font-size:9.5px;letter-spacing:.3px;color:#888;padding:4px 13px}
.btn-login{left:848px;top:18px;width:60px;height:21px;background:var(--orange);border-radius:3px;color:#fff;font:10px "Alfa Slab One",serif;text-align:center;line-height:21px}
.util{top:54px;font-size:9.5px;letter-spacing:.4px;color:#333}
.util-sep{left:799px;top:51px;width:1px;height:17px;background:#999}

/* nav */
.nav{left:101px;top:145px;display:flex;height:30px;font-family:"Questrial",sans-serif;font-size:11px}
.nav a{color:var(--link);text-decoration:none;line-height:30px;padding:0 9px;margin-right:6px}
.nav a.active{background:var(--navy);color:#fff}

/* announcement */
.announce{left:100px;top:193px;width:808px;height:53px;background:var(--navy)}
.announce-inner{left:104px;top:196px;width:606px;height:47px;background:#fff;border:1px solid var(--navy)}
.announce-label{left:126px;top:212px;font-family:"Questrial",sans-serif;font-size:11px;color:var(--orange)}
.announce-text{left:256px;top:212px;font-size:9.5px;letter-spacing:.4px;color:#222}
.search-label{left:777px;top:201px;font-family:"Questrial",sans-serif;font-size:10px;color:var(--orange)}
.search-box{left:737px;top:220px;width:148px;height:15px;background:#fff;border-radius:8px}
.search-btn{left:861px;top:220px;width:24px;height:15px;background:var(--orange);border-radius:8px}

/* frame */
.frame{left:100px;top:246px;width:808px;height:666px;border-left:1px solid var(--rule);border-right:1px solid var(--rule)}
.sidebar{left:100px;top:246px;width:182px;height:666px;background:var(--side)}
.side-nav{left:100px;top:276px;width:182px;font-family:"Questrial",sans-serif;font-size:11px}
.side-nav div{height:25.2px;line-height:25px;padding-left:17px;color:var(--link);position:relative}
.side-nav div::after{content:"›";position:absolute;right:15px;font-size:15px;top:-2px}
.side-nav div.current{background:var(--navy);color:#fff}
.dots{left:113px;width:155px;border-top:1px dotted #9fb3da}
.tender{left:113px;top:572px;width:157px;height:57px;background:var(--navy);border:1px solid #052a6e;border-radius:2px;text-align:center;color:#fff}
.tender b{display:block;font:15px "Alfa Slab One",serif;color:var(--orange);margin-top:10px}
.tender span{font-size:10px;letter-spacing:.4px}
.side-title{left:113px;font-family:"Questrial",sans-serif;font-size:14px;color:#444}
.side-list{left:122px;list-style:none;font-size:9.5px;letter-spacing:.5px;color:var(--link);line-height:15px}
.side-list li::before{content:"";display:inline-block;width:4px;height:4px;border:1.2px solid var(--orange);border-radius:50%;margin-right:7px;vertical-align:1px}

/* content */
.crumb{left:307px;top:262px;font-size:9.5px;letter-spacing:.4px;color:#888}
.crumb b{font-weight:400;color:#333}
.page-title{left:307px;top:290px;font-family:"Questrial",sans-serif;font-size:22px;font-weight:400;color:#1b2a5a}
.sec-title{left:307px;font-family:"Questrial",sans-serif;font-size:15px;font-weight:400;color:var(--orange)}
.rule{left:307px;width:580px;height:1px;background:var(--rule)}
.body-text{left:307px;width:575px;font-size:9.4px;letter-spacing:.35px;line-height:11.2px;color:#333}
.btn{left:800px;width:84px;height:22px;background:var(--navy);color:#fff;font-size:9.5px;letter-spacing:.4px;text-align:center;line-height:22px;border-radius:1px}
.photo{left:304px;top:681px;width:308px;height:154px;border:2px solid #b8b8b8;background:linear-gradient(135deg,#7fa0d8,#c9d8f0 55%,#8eabdd)}
.ticks{left:650px;top:685px;list-style:none;font-size:9.5px;letter-spacing:.45px;line-height:20.2px;color:#333}
.ticks svg{vertical-align:-2px;margin-right:8px}
.more{left:798px;top:833px;font-size:9.5px;letter-spacing:.4px;font-weight:700;font-style:italic;color:var(--link)}

/* partners */
.partners{left:100px;top:912px;width:808px;height:115px;border:1px solid var(--rule);border-bottom:none;display:flex;align-items:center;justify-content:space-around;font-family:"Questrial",sans-serif;font-size:13px;color:var(--navy-dark)}
.partners span{display:flex;align-items:center;gap:6px}
.partners i{width:14px;height:14px;border-radius:50%;background:var(--navy);display:inline-block}

/* footer */
.footer{left:100px;top:1027px;width:808px;height:173px;background:var(--footer)}
.foot-nav{left:128px;top:1051px;display:flex;gap:22px;font-size:9.5px;letter-spacing:.3px;color:var(--link)}
.foot-mark{left:128px;top:1088px;width:40px;height:40px;border-radius:50%;background:var(--navy)}
.foot-name{left:128px;top:1138px;font-family:"Questrial",sans-serif;font-size:13px;color:var(--navy-dark)}
.copy{left:128px;top:1165px;font-family:"Questrial",sans-serif;font-size:9.5px;color:#666}
.connect-title{left:689px;top:1047px;font-family:"Questrial",sans-serif;font-size:14px;color:#333}
.tweet{left:689px;top:1069px;width:195px;height:86px;background:#fff;border:1px solid #ddd;padding:13px 12px;font-size:8.4px;letter-spacing:.3px;line-height:10.5px;color:#333}
.tweet .meta{margin-top:7px;color:#c33}
.tweet .meta em{margin-left:8px}
.social{top:1162px;width:24px;height:24px;border-radius:50%;background:var(--navy);border:2px solid #e4e9f5}
</style>
</head>
<body>

<header>
  <div class="abs brand-mark"></div>
  <div class="abs brand-name">The Pelworth Shipping Association</div>
  <div class="abs login-label">MEMBER LOGIN:</div>
  <div class="abs field" style="left:506px">User ID</div>
  <div class="abs field" style="left:675px">Password</div>
  <div class="abs btn-login">LOG IN</div>
  <div class="abs util" style="left:737px">Register</div>
  <div class="abs util-sep"></div>
  <div class="abs util" style="left:818px">Forgot password?</div>
</header>

<nav class="abs nav">
  <a class="active">ABOUT US</a><a>SHIPPING SCHEDULE</a><a>NEWS</a><a>FAQ</a><a style="margin-right:16px">CONTACT US</a><a style="margin-right:16px">CANINE SERVICES</a><a style="margin-right:16px">PORTAVA</a><a>LINKS</a>
</nav>

<section>
  <div class="abs announce"></div>
  <div class="abs announce-inner"></div>
  <div class="abs announce-label">ANNOUNCEMENTS:</div>
  <div class="abs announce-text">Welcome to the PLW's website: We work the Port of Halvern...</div>
  <div class="abs search-label">SEARCH SITE</div>
  <div class="abs search-box"></div>
  <div class="abs search-btn"><svg width="24" height="15" viewBox="0 0 24 15"><circle cx="11" cy="6.5" r="3" fill="none" stroke="#fff" stroke-width="1.5"/><line x1="13" y1="8.5" x2="16" y2="11.5" stroke="#fff" stroke-width="2"/></svg></div>
</section>

<div class="abs frame"></div>
<aside>
  <div class="abs sidebar"></div>
  <div class="abs side-nav">
    <div class="current">HOME</div><div>ABOUT US</div><div>HOW WE WORK</div><div>OUR SERVICES</div><div>WHY US</div><div>NEWS AND UPDATES</div><div>ABOUT ORGANISATIONS</div><div>ABOUT MEMBERS</div><div>FAQS</div><div>CONTACT US</div>
  </div>
  <div class="abs dots" style="top:551px"></div>
  <div class="abs tender"><b>OPEN TENDERS</b><span>Register With PLW Now</span></div>
  <div class="abs dots" style="top:650px"></div>
  <div class="abs side-title" style="top:680px">Links</div>
  <ul class="abs side-list" style="top:704px"><li>Training Courses</li><li>About the Port of Halvern</li><li>Open Tenders</li></ul>
  <div class="abs side-title" style="top:790px">Important Facts</div>
  <ul class="abs side-list" style="top:814px"><li>Laws and Legislation</li><li>International trade Docs</li><li>Port Statistics</li><li>Shipping Terms</li></ul>
</aside>

<main>
  <div class="abs crumb">Home &gt; <b>About Us</b></div>
  <h1 class="abs page-title">ABOUT US</h1>

  <h2 class="abs sec-title" style="top:360px">About Us</h2>
  <div class="abs rule" style="top:385px"></div>
  <p class="abs body-text" style="top:401px">Fusce quis lacus diam, sit amet sollicitudin ante. Quisque ultricies dolor sit amet enim malesuada consectetur. Maece vulputate tellus nec orci posuere interdum. Suspendisse potenti. Fusce qis enim massa. Ut tempor turpis non dolor vel tempus ligula malesuada nibh erat, euismod ac interdum non, lacinia eu massa. Maecenas vulputate tellus nec posuere interdum. Suspendisse potenti. Fusce qis enim massa. Ut tempor turpis non dolor feugiat.</p>
  <div class="abs btn" style="top:462px">Read More</div>

  <h2 class="abs sec-title" style="top:510px">Lorem Ipsum Title</h2>
  <div class="abs rule" style="top:537px"></div>
  <p class="abs body-text" style="top:551px">Fusce quis lacus diam, sit amet sollicitudin ante. Quisque ultricies dolor sit amet enim malesuada consectetur. Maec vulputate tellus nec orci posuere interdum. Suspendisse potenti. Fusce qis enim massa. Ut tempor turpis non dolor vel tempus ligula malesuada nibh erat, euismod ac interdum non, lacinia eu massa. Maecenas vulputate tellus nec posuere interdum. Suspendisse potenti. Fusce qis enim massa. Ut tempor turpis non dolor feugiat.</p>
  <div class="abs btn" style="top:618px">Read More</div>

  <h2 class="abs sec-title" style="top:652px">How We Work</h2>
  <div class="abs photo" role="img" aria-label="Photo of a pen tracing a line chart on a financial report, blue toned"></div>
  <ul class="abs ticks">
    <li><svg width="13" height="11" viewBox="0 0 13 11"><path d="M1 6l4 4 7-9" fill="none" stroke="#f4a20a" stroke-width="2.4"/></svg>Fusce quis lacus diam, sit amet sollicitudin</li>
    <li><svg width="13" height="11" viewBox="0 0 13 11"><path d="M1 6l4 4 7-9" fill="none" stroke="#f4a20a" stroke-width="2.4"/></svg>Quisque ultricies dolor sit amet enim male</li>
    <li><svg width="13" height="11" viewBox="0 0 13 11"><path d="M1 6l4 4 7-9" fill="none" stroke="#f4a20a" stroke-width="2.4"/></svg>Maecenas vulputate tellus nec orci posuere</li>
    <li><svg width="13" height="11" viewBox="0 0 13 11"><path d="M1 6l4 4 7-9" fill="none" stroke="#f4a20a" stroke-width="2.4"/></svg>Suspendisse potenti eusce qis enim massa</li>
    <li><svg width="13" height="11" viewBox="0 0 13 11"><path d="M1 6l4 4 7-9" fill="none" stroke="#f4a20a" stroke-width="2.4"/></svg>Ut tempor turpis non dolor feugiat</li>
    <li><svg width="13" height="11" viewBox="0 0 13 11"><path d="M1 6l4 4 7-9" fill="none" stroke="#f4a20a" stroke-width="2.4"/></svg>Maecenas vulputate tellus nec orci posure</li>
    <li><svg width="13" height="11" viewBox="0 0 13 11"><path d="M1 6l4 4 7-9" fill="none" stroke="#f4a20a" stroke-width="2.4"/></svg>Suspendisse potenti qis enim massa</li>
  </ul>
  <div class="abs more">Find out more...</div>
</main>

<section class="abs partners">
  <span><i></i>Meridel Lines</span>
  <span><i></i>Tidewell</span>
  <span><i></i>Harbex Shipping Co.</span>
  <span><i></i>Norvik Shipping</span>
  <span><i></i>Calloway Intl Shipping</span>
</section>

<footer>
  <div class="abs footer"></div>
  <div class="abs foot-nav"><span>Shipping Schedule</span><span>News</span><span>Faq</span><span>Contact Us</span><span>Canine Services</span><span>Portava</span><span>Links</span></div>
  <div class="abs foot-mark"></div>
  <div class="abs foot-name">The Pelworth Shipping Association</div>
  <div class="abs copy">© Copyright 2012. All Rights Reserved.</div>
  <div class="abs connect-title">Connect With Us</div>
  <div class="abs tweet">Praesent tempus sagittis elementum. Prsent id quam erat, sit amet condi mentum neque. Phasellus quis est nisi. Ut luctus adipiscing.
    <div class="meta">Lorem Ipsum <em>2 hours ago</em></div></div>
  <div class="abs social" style="left:692px"></div>
  <div class="abs social" style="left:722px"></div>
  <div class="abs social" style="left:751px"></div>
  <div class="abs social" style="left:782px"></div>
</footer>

</body>
</html>
```